Meadow Paw Web Site

We have basically a start up business that I need help with. This project is just for the web site.

Our product is a frozen raw pet food that promotes weight control, less shedding, smaller stools and an overall better health. The product is in nugget form similar to what you would see in a steak shish kabob. I only share that with you in case you want to incorporate that in the design.

We have been in business for 17 years but all of our sales have been word of mouth. We are going to be launching an infomercial this summer and I need everything stated previously to be completed before we can launch the infomercial.

We need the following (6) pages:

Home:
This is where we need to have the ability to purchase our products. Our main goal is to get the consumer to purchase our product. We have our own shopping cart so we just need to allow for the insertion of that shopping cart.

Why Raw:
This will just be a page with 4-5 paragraphs and an embedded YouTube video.

How to Use:
We will need a page with a chart (4 Columns wide with 6 rows) as well as an embedded YouTube video.

Customer Success Stories:
Allow us to add these as we move forward. I need a placeholder for an image of the customers pet and a paragraph or two explaining the situation

Where to Buy:
- Online - Find a Retailer - Find a Local Distributor - Call to Order

Contact Us:
Copper Ridge Holdings, Inc.
2740 Copper Rd
Eagan, MN 55148
(800) xxx-xxxx

We need to provide links to our to be created... Facebook page, Twitter Account, Youtube Channel, Google circle, Blog
Updates

All, I have received many front page designs that look good.  Please notice in the brief that I need multiple pages built not just the home page.  

Thanks,

Dale

Reason: I need to see the rest of the pages. Thanks, Dale

Target Market(s)

Women between the ages of 30 & 60.

Industry/Entity Type

Shopping

```html
<!DOCTYPE html>
<html lang="en">
<head>
<meta charset="utf-8">
<title>Meadow Paw — Client Testimonials</title>
<link rel="stylesheet" href="https://fonts.googleapis.com/css2?family=Oswald:wght@400;500&family=Open+Sans:wght@400;600&display=swap">
<style>
:root{
  --orange:#e06a0a;
  --orange-dark:#b94a05;
  --orange-light:#f39a2c;
  --rust:#c0440a;
  --yellow:#f7d21c;
  --page:#fbf5f5;
  --ink:#333;
  --footer:#2c2c2e;
  --footer-bottom:#1d1d1f;
  --footer-text:#a9a9ad;
  --white:#fff;
}
*{margin:0;padding:0;box-sizing:border-box}
html,body{width:670px;height:1200px;overflow:hidden}
body{position:relative;background:var(--page);font-family:"Open Sans",Arial,sans-serif;color:var(--ink)}
.abs{position:absolute}
.hero-band{left:0;top:0;width:670px;height:341px;background:radial-gradient(ellipse at 50% 45%,#f6f5f4 0%,#e3e1df 60%,#cfcdcb 100%)}
.top-links{right:69px;top:13px;font:600 6.5px "Open Sans",sans-serif;color:var(--rust);letter-spacing:.2px}
.top-links span{margin:0 3px}
.btn{height:14px;border-radius:7px;font:400 8px "Open Sans",sans-serif;text-align:center;line-height:14px}
.btn-signin{left:505px;top:36px;width:46px;background:linear-gradient(#f08a20,var(--orange-dark));color:var(--white)}
.btn-register{left:556px;top:36px;width:47px;background:linear-gradient(#fde458,#f0c20d);color:#5a3a00}
.brand{left:67px;top:34px;display:flex;align-items:center;gap:6px}
.brand-mark{width:22px;height:22px;background:var(--orange)}
.brand-name{font:500 22px "Oswald",sans-serif;color:var(--orange-dark)}
.cart{left:348px;top:67px;display:flex;align-items:center;font:400 7.5px "Oswald",sans-serif;color:var(--rust)}
.cart-items{left:438px;top:69px;font:400 7.5px "Oswald",sans-serif;color:var(--rust)}
.search{left:483px;top:66px;width:119px;height:17px;border-radius:9px;background:var(--white);border:1px solid #e1d3c8;font:400 7px "Open Sans",sans-serif;color:#444;padding:3px 10px}
.search svg{position:absolute;right:8px;top:3px}
.main-nav{left:67px;top:96px;width:535px;height:26px;border-radius:4px;background:linear-gradient(#f28a1e,var(--orange) 55%,#c85a06);display:flex}
.main-nav a{color:var(--white);text-decoration:none;font:400 10.5px "Oswald",sans-serif;display:flex;align-items:center;justify-content:center;border-right:1px solid #c05405}
.main-nav a:last-child{border-right:0}
.slider-frame{left:67px;top:134px;width:375px;height:182px;border-radius:8px;background:#d5977a}
.slider-image{left:75px;top:142px;width:359px;height:166px;background:linear-gradient(180deg,#7aa04a 0%,#a8a257 35%,#d8a866 70%,#c9843c 100%)}
.slider-caption{right:248px;top:244px;text-align:right;font:400 17px/24px "Oswald",sans-serif;color:var(--white);text-shadow:0 1px 2px rgba(0,0,0,.45)}
.dots{left:229px;top:324px;display:flex;gap:4px}
.dots i{width:7px;height:7px;border-radius:50%;background:var(--white);display:block}
.dots i.active{background:var(--orange)}
.order-panel{left:456px;top:134px;width:146px;height:182px;border-radius:6px;overflow:hidden}
.order-image{width:146px;height:155px;background:linear-gradient(180deg,#6f6450 0%,#a8906a 50%,#7aa845 100%)}
.order-band{height:27px;background:linear-gradient(#f08a20,var(--orange-dark));color:var(--white);font:400 14px/27px "Oswald",sans-serif;text-align:center;letter-spacing:.5px}
.section-title{left:67px;top:355px;width:535px;height:23px;border-radius:4px;background:linear-gradient(#f28a1e,var(--orange) 55%,#c85a06);color:var(--white);font:400 11px/23px "Oswald",sans-serif;padding-left:12px}
.testimonial{left:67px;width:535px;height:140px;background:var(--white);border-bottom:2px solid #d8d3d3}
.testimonial-photo{position:absolute;left:3px;top:3px;width:185px;height:135px}
.t1 .testimonial-photo{background:linear-gradient(90deg,#e8dccd,#c9a080 60%,#d66a3a)}
.t2 .testimonial-photo{background:linear-gradient(135deg,#efeae4,#9a8e80 55%,#3c4656)}
.t3 .testimonial-photo{background:linear-gradient(90deg,#8a7b6e,#d9cfc4 60%,#ece7e1)}
.t4 .testimonial-photo{background:linear-gradient(135deg,#fbf2e0,#e0b77c 55%,#b87a3d)}
.testimonial blockquote{position:absolute;left:219px;top:25px;width:303px;font:400 9.2px/13.6px "Open Sans",sans-serif;color:#333}
.quote-open,.quote-close{font:700 26px/1 Georgia,serif;color:var(--rust);position:absolute}
.quote-open{left:198px;top:16px}
.testimonial cite{position:absolute;right:18px;top:106px;font:500 9.5px "Oswald",sans-serif;color:#111;font-style:normal}
.footer{left:0;top:1022px;width:670px;height:154px;background:var(--footer)}
.footer-col{position:absolute;top:18px}
.footer-col h3{font:400 11px "Oswald",sans-serif;color:var(--white);margin-bottom:6px}
.footer-col li{list-style:none;font:400 7px/13.4px "Open Sans",sans-serif;color:var(--footer-text)}
.divider{position:absolute;top:22px;height:128px;border-left:1px dotted #555}
.contact-line{font:400 7.5px "Open Sans",sans-serif;color:var(--footer-text)}
.contact-small{font:400 6px/10px "Open Sans",sans-serif;color:var(--footer-text);width:110px;margin-top:3px}
.phone{display:flex;align-items:center;gap:4px;margin-top:8px;font:400 7.5px "Open Sans",sans-serif;color:var(--footer-text)}
.email{position:absolute;left:0;top:48px;width:132px;height:18px;background:var(--white);border-radius:2px;font:400 7.5px/18px "Open Sans",sans-serif;color:#aaa;padding-left:7px}
.subscribe{position:absolute;left:84px;top:70px;width:48px;height:16px;background:var(--orange-dark);color:var(--white);font:400 8.5px/16px "Open Sans",sans-serif;text-align:center;border-radius:1px}
.socials{position:absolute;left:40px;top:94px;display:flex;gap:4px}
.socials i{display:block;width:15px;height:15px;border-radius:2px;background:var(--orange)}
.footer-bottom{left:0;top:1176px;width:670px;height:24px;background:var(--footer-bottom);font:400 6.5px/24px "Open Sans",sans-serif;color:#777;padding-left:67px}
</style>
</head>
<body>
<div class="abs hero-band"></div>

<nav class="abs top-links">MY ACCOUNT<span>/</span>WISH LIST<span>/</span>MY CART<span>/</span>CHECKOUT</nav>
<div class="abs btn btn-signin">Sing in</div>
<div class="abs btn btn-register">Register</div>

<div class="abs brand"><span class="brand-mark"></span><span class="brand-name">Meadow Paw</span></div>

<div class="abs cart">
  <svg width="16" height="12" viewBox="0 0 16 12"><path d="M1 3h14l-2 8H3z" fill="none" stroke="#c0440a" stroke-width="1.5"/><path d="M5 3l3-2.5L11 3" fill="none" stroke="#c0440a" stroke-width="1.2"/></svg>
  <span style="margin-left:6px">SHOPPING CART</span>
</div>
<div class="abs cart-items">(2) ITEMS</div>
<div class="abs search">Search.......
  <svg width="10" height="10" viewBox="0 0 10 10"><circle cx="4" cy="4" r="3" fill="none" stroke="#c0440a" stroke-width="1.6"/><path d="M6 6l3 3" stroke="#c0440a" stroke-width="1.8"/></svg>
</div>

<nav class="abs main-nav">
  <a style="width:43px" aria-label="Home"><svg width="12" height="11" viewBox="0 0 12 11"><path d="M6 0L0 5h1.5v6h3.5V7.5h2V11h3.5V5H12z" fill="#fff"/></svg></a>
  <a style="width:81px">Why Raw</a>
  <a style="width:96px">How to Use</a>
  <a style="width:107px">Where to Buy</a>
  <a style="width:120px">Success Stories</a>
  <a style="width:88px">Contact Us</a>
</nav>

<div class="abs slider-frame"></div>
<div class="abs slider-image" role="img" aria-label="Three golden retriever puppies resting on a wooden ledge in front of grass"></div>
<div class="abs slider-caption">There are many variations of<br>passages of Lorem</div>
<div class="abs dots"><i></i><i></i><i class="active"></i><i></i><i></i></div>

<div class="abs order-panel">
  <div class="order-image" role="img" aria-label="Puppy running across a lawn"></div>
  <div class="order-band">CALL TO ORDER</div>
</div>

<h2 class="abs section-title">Our client testimonials</h2>

<article class="abs testimonial t1" style="top:392px">
  <div class="testimonial-photo" role="img" aria-label="Woman smiling next to her small long-haired dog"></div>
  <span class="quote-open">“</span>
  <blockquote>Lorem ipsum dolor sit amet, consectetur adipiscing elit. Nulla ornare, nisi ut interdum condimentum, felis lectus pharetra nunc, nec tristique quam mi eu nunc. Nulla ornare sagittis ante, id sollicitudin nunc. Vestibulum ut sodales nisi. Pellentesque nunc dolor, faucibus in erat a, hendrerit mattis elit. Duis ornare mi ut risus egestas malesuada. <span style="font:700 22px/0 Georgia,serif;color:var(--rust);vertical-align:-8px">”</span></blockquote>
  <cite>– Client Name Here</cite>
</article>

<article class="abs testimonial t2" style="top:548px">
  <div class="testimonial-photo" role="img" aria-label="Young couple sitting on the floor with their small dog"></div>
  <span class="quote-open">“</span>
  <blockquote>Lorem ipsum dolor sit amet, consectetur adipiscing elit. Nulla ornare, nisi ut interdum condimentum, felis lectus pharetra nunc, nec tristique quam mi eu nunc. Nulla ornare sagittis ante, id sollicitudin nunc. Vestibulum ut sodales nisi. Pellentesque nunc dolor, faucibus in erat a, hendrerit mattis elit. Duis ornare mi ut risus egestas malesuada. <span style="font:700 22px/0 Georgia,serif;color:var(--rust);vertical-align:-8px">”</span></blockquote>
  <cite>– Client Name Here</cite>
</article>

<article class="abs testimonial t3" style="top:704px">
  <div class="testimonial-photo" role="img" aria-label="Older man resting his head against a bulldog"></div>
  <span class="quote-open">“</span>
  <blockquote>Lorem ipsum dolor sit amet, consectetur adipiscing elit. Nulla ornare, nisi ut interdum condimentum, felis lectus pharetra nunc, nec tristique quam mi eu nunc. Nulla ornare sagittis ante, id sollicitudin nunc. Vestibulum ut sodales nisi. Pellentesque nunc dolor, faucibus in erat a, hendrerit mattis elit. Duis ornare mi ut risus egestas malesuada. <span style="font:700 22px/0 Georgia,serif;color:var(--rust);vertical-align:-8px">”</span></blockquote>
  <cite>– Client Name Here</cite>
</article>

<article class="abs testimonial t4" style="top:860px">
  <div class="testimonial-photo" role="img" aria-label="Woman hugging her golden retriever"></div>
  <span class="quote-open">“</span>
  <blockquote>Lorem ipsum dolor sit amet, consectetur adipiscing elit. Nulla ornare, nisi ut interdum condimentum, felis lectus pharetra nunc, nec tristique quam mi eu nunc. Nulla ornare sagittis ante, id sollicitudin nunc. Vestibulum ut sodales nisi. Pellentesque nunc dolor, faucibus in erat a, hendrerit mattis elit. Duis ornare mi ut risus egestas malesuada. <span style="font:700 22px/0 Georgia,serif;color:var(--rust);vertical-align:-8px">”</span></blockquote>
  <cite>– Client Name Here</cite>
</article>

<footer class="abs footer">
  <div class="footer-col" style="left:67px"><h3>Quick Links</h3><ul><li>Why Raw</li><li>How to Use</li><li>Where to Buy</li><li>Success Stories</li><li>How to Use</li><li>Where to Buy</li><li>Contact Us</li></ul></div>
  <div class="divider" style="left:136px"></div>
  <div class="footer-col" style="left:153px"><h3>Top Products</h3><ul><li>Product 1</li><li>Product 2</li><li>Product 3</li><li>Product 4</li><li>Product 5</li><li>Product 6</li><li>Product 7</li></ul></div>
  <div class="divider" style="left:222px"></div>
  <div class="footer-col" style="left:239px"><h3>Where to Buy</h3><ul><li>Find a Retailer</li><li>Find a Local Distributor</li><li>Call to Order</li></ul></div>
  <div class="divider" style="left:325px"></div>
  <div class="footer-col" style="left:344px"><h3>Contact Information</h3>
    <div class="contact-line">PUBLISHING PACKAGES</div>
    <div class="contact-small">Lorem Ipsum is therefore always free from repetition</div>
    <div class="phone"><svg width="9" height="10" viewBox="0 0 9 10"><path d="M2 0l2 2.5-1.2 1.3c.6 1.3 1.4 2.1 2.6 2.7L6.6 5.3 9 7.3 7.6 9.5C3.5 9 0 5.5 0 1.5z" fill="#ccc"/></svg>+0 (000) 000-0000</div>
  </div>
  <div class="divider" style="left:454px"></div>
  <div class="footer-col" style="left:470px;width:132px"><h3>Newsletter</h3>
    <div class="contact-small" style="font-size:6.8px;line-height:9px;width:132px">combined with a handful of model sentence structures.</div>
    <div class="email">Email address</div>
    <div class="subscribe">Subscribe</div>
    <div class="socials" aria-label="Social links"><i></i><i></i><i></i><i></i><i></i></div>
  </div>
</footer>
<div class="abs footer-bottom">Company Name © 2014. Privacy Policy</div>
</body>
</html>
```